CV design and layout with option for text and contact details has be sleek

I have logo just need this to look good on a CV

Target Market(s)

Directors , Production , TV, Film

Industry/Entity Type

tv film cinema advertising

Colors
0054AA
0677BA
7BADD7
CADEEF
E8F1F8

Requirements
Must have
• my logo and contact information
Should not have
• any other images or logos except mine

```html
<!DOCTYPE html>
<html lang="en">
<head>
<meta charset="UTF-8">
<title>Rowan Ellery DOP – Cinematographer Signature</title>
<link rel="stylesheet" href="https://fonts.googleapis.com/css2?family=Montserrat:wght@400;500;700&display=swap">
<style>
  :root {
    --paper: #ffffff;
    --ink: #000000;
    --label: #333333;
    --accent: #0677ea;
  }
  * { box-sizing: border-box; margin: 0; padding: 0; }
  html, body {
    width: 1200px; height: 1200px; overflow: hidden;
    background: var(--paper);
    font-family: "Montserrat", sans-serif;
  }
  .canvas { position: relative; width: 1200px; height: 1200px; }
  .signature {
    position: absolute; left: 152px; top: 493px;
    width: 896px; height: 213px;
    display: flex;
  }
  .brand-panel {
    width: 350px; height: 100%;
    background: var(--ink);
    display: flex; align-items: center; justify-content: center;
  }
  .brand-name {
    color: var(--paper);
    font-weight: 400; font-size: 28px; letter-spacing: 0.2px;
    white-space: nowrap;
  }
  .contact-panel {
    flex: 1; height: 100%;
    border: 2px solid var(--ink); border-left: none;
    padding: 19px 0 0 35px;
  }
  .role {
    color: var(--label);
    font-weight: 700; font-size: 18.5px; letter-spacing: 0.6px;
    line-height: 1; margin-bottom: 10px;
  }
  .contact-list { list-style: none; }
  .contact-item {
    display: flex; align-items: center;
    height: 28.4px;
    font-size: 19.5px; font-weight: 500; color: var(--label);
    white-space: nowrap;
  }
  .icon-box {
    width: 25px; height: 25px; flex: none;
    border: 2px solid var(--ink);
    display: flex; align-items: center; justify-content: center;
    margin-right: 11px;
  }
  .icon-box svg { width: 17px; height: 17px; }
  .value { color: var(--accent); margin-left: 6px; }
  .value.solo { margin-left: 0; }
</style>
</head>
<body>
<div class="canvas">
  <section class="signature">
    <div class="brand-panel">
      <span class="brand-name">ROWAN ELLERY DOP</span>
    </div>
    <div class="contact-panel">
      <p class="role">CINEMATOGRAPHER</p>
      <ul class="contact-list">
        <li class="contact-item">
          <span class="icon-box"><svg viewBox="0 0 24 24"><path d="M7 3 L10 7 L8 9.5 C9 12 11.5 14.5 14 15.5 L16.5 13.5 L20.5 16.5 L18.5 20 C11 20 4 13 4 5.5 Z" fill="none" stroke="#000" stroke-width="2" stroke-linejoin="round"/></svg></span>
          MOB AUS<span class="value">+61 400 555 019</span>
        </li>
        <li class="contact-item">
          <span class="icon-box"><svg viewBox="0 0 24 24"><path d="M7 3 L10 7 L8 9.5 C9 12 11.5 14.5 14 15.5 L16.5 13.5 L20.5 16.5 L18.5 20 C11 20 4 13 4 5.5 Z" fill="none" stroke="#000" stroke-width="2" stroke-linejoin="round"/></svg></span>
          MOB US<span class="value">+1 424 555 0182</span>
        </li>
        <li class="contact-item">
          <span class="icon-box"><svg viewBox="0 0 24 24"><path d="M7 3 L10 7 L8 9.5 C9 12 11.5 14.5 14 15.5 L16.5 13.5 L20.5 16.5 L18.5 20 C11 20 4 13 4 5.5 Z" fill="none" stroke="#000" stroke-width="2" stroke-linejoin="round"/></svg></span>
          AGENT CREWLINE:<span class="value">+61 290 555 104</span>
        </li>
        <li class="contact-item">
          <span class="icon-box"><svg viewBox="0 0 24 24"><rect x="2" y="5" width="20" height="14" fill="none" stroke="#000" stroke-width="2"/><path d="M2 5 L12 13 L22 5 M2 19 L9 11 M22 19 L15 11" fill="none" stroke="#000" stroke-width="1.6"/></svg></span>
          <span class="value solo">rowanellerydop@example.com</span>
        </li>
        <li class="contact-item">
          <span class="icon-box"><svg viewBox="0 0 24 24"><circle cx="12" cy="12" r="9" fill="none" stroke="#000" stroke-width="2"/><ellipse cx="12" cy="12" rx="4" ry="9" fill="none" stroke="#000" stroke-width="1.5"/><path d="M3 12 H21 M5 7.5 H19 M5 16.5 H19" stroke="#000" stroke-width="1.5"/></svg></span>
          <span class="value solo">www.rowanellery.com.au</span>
        </li>
      </ul>
    </div>
  </section>
</div>
</body>
</html>
```